BMR Going Cashless

Hello,
We are a medical office looking to get a flyer created to promote to our patients we will be going "Cashless." Our tagline will be "Cash-Less is Stress-Less"

"Starting in July, to offer you the fastest and most convenient service, we are transitioning to a cashless system. You can now enjoy faster checkout times and greater security with card and contactless payments. More info to come."

I've added two other flyers as sample designs we've used.

Please include logo, addresses, website, phone number

Files to include jpeg, png, pdf (under 5mb), Facebook and Instagram sizing.

Thank you,
Lowen

```html
<!DOCTYPE html>
<html lang="en">
<head>
<meta charset="utf-8">
<title>BMR Foot Care – Cash-less is Stress-less</title>
<link rel="stylesheet" href="https://fonts.googleapis.com/css2?family=Bebas+Neue&family=Poppins:wght@300;400;500;600;700;800;900&display=swap">
<style>
:root{
  --board:#ebebeb;
  --white:#ffffff;
  --orange:#f47c45;
  --teal:#4fbf9c;
  --teal-echo:#d5eee5;
  --chalk:#2b2b2b;
  --chalk-light:#363636;
  --ink:#2a2a2a;
  --label:#2f2f2f;
}
*{margin:0;padding:0;box-sizing:border-box}
html,body{width:946px;height:1200px;overflow:hidden;background:var(--board)}
body{position:relative;font-family:"Poppins",sans-serif;color:var(--white)}

.artboard{position:absolute;overflow:hidden;background:var(--white);box-shadow:0 6px 22px rgba(0,0,0,.18)}
.artboard--square{left:244px;top:66px;width:460px;height:461px}
.artboard--wide{left:52px;top:625px;width:844px;height:461px}

.size-label{position:absolute;left:0;width:946px;text-align:center;font-family:"Poppins",sans-serif;font-weight:300;font-size:24px;color:var(--label);letter-spacing:.5px}
.size-label--square{top:548px}
.size-label--wide{top:1102px}

.chalkboard{position:absolute;left:0;right:0;bottom:0;background:radial-gradient(ellipse at 40% 60%,var(--chalk-light),var(--chalk) 70%)}
.torn-edge{position:absolute;left:0;width:100%}
.photo{position:absolute}

.headline{position:absolute;font-family:"Bebas Neue",sans-serif;color:var(--orange);line-height:1;white-space:nowrap}
.subline{position:absolute;font-family:"Poppins",sans-serif;font-weight:900;color:var(--teal);line-height:1;white-space:nowrap;text-shadow:0 4px 0 var(--teal-echo),0 8px 0 #edf7f3}

.brand{position:absolute;display:flex;align-items:center;gap:6px}
.brand__dot{border-radius:50%;background:var(--teal);flex:none}
.brand__name{font-family:"Poppins",sans-serif;font-weight:700;color:var(--orange);line-height:1.05;text-transform:uppercase}

.start{position:absolute;font-weight:700;color:var(--teal);white-space:nowrap;line-height:1}
.lead{position:absolute;font-weight:600;color:var(--white)}
.body-copy{position:absolute;font-weight:400;color:var(--white)}
.more-info{position:absolute;font-weight:700;letter-spacing:3px;color:var(--white)}

.offices{position:absolute;display:flex}
.office{display:flex;gap:5px}
.pin{flex:none}
.office__name{font-weight:600;color:var(--orange);text-transform:uppercase;line-height:1.3}
.office__addr{font-weight:400;color:var(--white);line-height:1.3}

.phone{position:absolute;display:flex;align-items:center;gap:5px;color:var(--white);line-height:1;white-space:nowrap}
.web-pill{position:absolute;background:var(--teal);color:var(--ink);font-weight:600;text-align:center;white-space:nowrap}

/* square */
.artboard--square .headline{left:0;width:460px;text-align:center;top:63px;font-size:84px}
.artboard--square .subline{left:0;width:460px;text-align:center;top:135px;font-size:43px}
.artboard--square .brand{left:160px;top:22px}
.artboard--square .brand__dot{width:26px;height:26px}
.artboard--square .brand__name{font-size:13px}
.artboard--square .chalkboard{top:240px}
.artboard--square .photo{left:0;top:182px;width:460px;height:88px;background:linear-gradient(90deg,#e3a982 0%,#c88b66 35%,#2f4fa8 45%,#2a2a2a 62%,#d9a07d 80%,#e7b28f 100%);opacity:.95}
.artboard--square .start{left:0;width:460px;text-align:center;top:268px;font-size:21px}
.artboard--square .lead{left:0;width:460px;text-align:center;top:292px;font-size:12.6px;line-height:12.5px}
.artboard--square .body-copy{left:0;width:460px;text-align:center;top:319px;font-size:9.4px;line-height:11px}
.artboard--square .more-info{left:0;width:460px;text-align:center;top:346px;font-size:11px}
.artboard--square .rule{position:absolute;left:40px;width:380px;top:364px;height:1px;background:var(--orange)}
.artboard--square .offices{left:46px;top:374px}
.artboard--square .office{width:135px}
.artboard--square .office:nth-child(2){width:123px}
.artboard--square .office__name{font-size:7px}
.artboard--square .office__addr{font-size:7px}
.artboard--square .phone{left:46px;top:412px;font-size:16.5px;font-weight:400;letter-spacing:.3px}
.artboard--square .web-pill{left:199px;top:412px;width:220px;height:18px;border-radius:9px;font-size:13.5px;line-height:18px;letter-spacing:2.2px}

/* wide */
.artboard--wide .photo{left:353px;top:0;width:491px;height:300px;background:linear-gradient(90deg,rgba(255,255,255,1) 0%,#d9d9d9 18%,#9a9a9a 45%,#5a5a5a 70%,#c99578 88%,#d8a585 100%)}
.artboard--wide .chalkboard{top:232px}
.artboard--wide .headline{left:35px;top:30px;font-size:116px;letter-spacing:-1px}
.artboard--wide .subline{left:35px;top:124px;font-size:66px}
.artboard--wide .start{left:35px;top:263px;font-size:34px;color:var(--white)}
.artboard--wide .start .in{color:var(--teal);font-weight:300}
.artboard--wide .start .july{color:var(--teal)}
.artboard--wide .lead{left:35px;top:310px;width:340px;font-size:15.6px;line-height:18px}
.artboard--wide .body-copy{left:35px;top:368px;width:345px;font-size:13.8px;line-height:16.5px}
.artboard--wide .divider{position:absolute;left:392px;top:270px;height:147px;border-left:1px dashed var(--orange)}
.artboard--wide .more-info{left:410px;top:262px;font-size:19.5px;font-weight:300;letter-spacing:0;line-height:19px}
.artboard--wide .more-info span{color:var(--orange)}
.artboard--wide .brand{left:540px;top:266px}
.artboard--wide .brand__dot{width:34px;height:34px}
.artboard--wide .brand__name{font-size:15px}
.artboard--wide .phone{left:410px;top:316px;font-size:28px;font-weight:300;letter-spacing:.5px}
.artboard--wide .offices{left:410px;top:351px}
.artboard--wide .office{width:145px}
.artboard--wide .office:nth-child(2){width:137px}
.artboard--wide .office__name{font-size:8.2px}
.artboard--wide .office__addr{font-size:8.2px}
.artboard--wide .web-pill{left:412px;top:396px;width:355px;height:25px;border-radius:10px;font-size:18px;line-height:25px;letter-spacing:5px}
</style>
</head>
<body>

<section class="artboard artboard--square" aria-label="Square post">
  <div class="chalkboard"></div>
  <div class="photo" role="img" aria-label="Photo of a hand passing a bank card to a hand holding a card payment terminal"></div>
  <svg class="torn-edge" style="top:225px" width="460" height="30" viewBox="0 0 460 30" preserveAspectRatio="none" aria-hidden="true">
    <path d="M0 0 H460 V4 L450 8 440 5 430 10 418 6 406 12 395 8 385 14 372 10 360 15 350 11 345 0 Z" fill="#fff" opacity="0"/>
  </svg>
  <div class="brand"><span class="brand__dot"></span><span class="brand__name">BMR<br>Foot Care</span></div>
  <h1 class="headline">CA$H-LESS IS</h1>
  <h2 class="subline">STRESS-LESS</h2>
  <p class="start">STARTING IN JULY</p>
  <p class="lead">to offer you the fastest and most convenient<br>service, we are transitioning to a cashless system.</p>
  <p class="body-copy">we are transitioning to a cashless system. You can now enjoy faster checkout<br>times and greater security with card and contactless payments.</p>
  <p class="more-info">MORE INFO TO COME</p>
  <div class="rule"></div>
  <div class="offices">
    <div class="office">
      <svg class="pin" width="15" height="15" viewBox="0 0 16 16" aria-hidden="true"><circle cx="8" cy="8" r="8" fill="#f47c45"/><path d="M8 3.5a3 3 0 0 0-3 3c0 2.2 3 5.5 3 5.5s3-3.3 3-5.5a3 3 0 0 0-3-3z" fill="#fff"/><circle cx="8" cy="6.5" r="1.1" fill="#f47c45"/></svg>
      <div><p class="office__name">Northfield Office</p><p class="office__addr">58 Linden Park Dr. Ste<br>120 Northfield, MD 21700</p></div>
    </div>
    <div class="office">
      <svg class="pin" width="15" height="15" viewBox="0 0 16 16" aria-hidden="true"><circle cx="8" cy="8" r="8" fill="#f47c45"/><path d="M8 3.5a3 3 0 0 0-3 3c0 2.2 3 5.5 3 5.5s3-3.3 3-5.5a3 3 0 0 0-3-3z" fill="#fff"/><circle cx="8" cy="6.5" r="1.1" fill="#f47c45"/></svg>
      <div><p class="office__name">Brookvale Office</p><p class="office__addr">2210 Maple Crest Blvd.<br>Ste. 305 Brookvale, MD 21799</p></div>
    </div>
    <div class="office">
      <svg class="pin" width="15" height="15" viewBox="0 0 16 16" aria-hidden="true"><circle cx="8" cy="8" r="8" fill="#f47c45"/><path d="M8 3.5a3 3 0 0 0-3 3c0 2.2 3 5.5 3 5.5s3-3.3 3-5.5a3 3 0 0 0-3-3z" fill="#fff"/><circle cx="8" cy="6.5" r="1.1" fill="#f47c45"/></svg>
      <div><p class="office__name">Riverton Office</p><p class="office__addr">47 Wellness Way<br>Riverton, WV 25499</p></div>
    </div>
  </div>
  <p class="phone">
    <svg width="15" height="15" viewBox="0 0 16 16" aria-hidden="true"><circle cx="8" cy="8" r="8" fill="#f47c45"/><path d="M5.2 4.2l1.4-.4 1 2.1-.9.8c.4 1 1.2 1.8 2.2 2.3l.8-.9 2.1 1-.4 1.4c-3 .2-6.4-3.2-6.2-6.3z" fill="#fff"/></svg>
    (555)010-0148
  </p>
  <p class="web-pill">www.bmrfootcare.com</p>
</section>
<p class="size-label size-label--square">1080 X 1080</p>

<section class="artboard artboard--wide" aria-label="Wide banner">
  <div class="photo" role="img" aria-label="Photo of a hand tapping a card on a payment terminal"></div>
  <div class="chalkboard"></div>
  <svg class="torn-edge" style="top:200px" width="844" height="70" viewBox="0 0 844 70" preserveAspectRatio="none" aria-hidden="true">
    <path d="M0 0 H500 V46 L488 40 476 50 462 42 450 52 436 44 420 54 406 45 392 50 378 40 362 48 346 38 330 44 314 34 298 40 280 30 262 38 246 30 228 36 210 28 192 36 176 30 158 38 140 32 122 40 104 34 86 42 68 36 50 44 32 38 16 46 0 40 Z" fill="#fff"/>
    <path d="M500 0 H844 V62 L832 66 818 58 804 64 790 56 774 62 760 54 744 60 728 52 712 58 696 50 680 56 664 48 648 54 632 46 616 52 600 44 584 50 568 42 552 48 536 40 520 46 500 40 Z" fill="#8d8d8d" opacity=".35"/>
  </svg>
  <h1 class="headline">CA$H-LESS IS</h1>
  <h2 class="subline">STRESS-LESS</h2>
  <p class="start">STARTING <span class="in">IN</span> <span class="july">JULY</span></p>
  <p class="lead">to offer you the fastest and most convenient service, we are transitioning to a cashless system.</p>
  <p class="body-copy">we are transitioning to a cashless system. You can now enjoy faster checkout times and greater security with card and contactless payments.</p>
  <div class="divider"></div>
  <p class="more-info"><span>MORE INFO</span><br>TO COME..</p>
  <div class="brand"><span class="brand__dot"></span><span class="brand__name">BMR<br>Foot Care</span></div>
  <p class="phone">
    <svg width="18" height="18" viewBox="0 0 16 16" aria-hidden="true"><circle cx="8" cy="8" r="8" fill="#f47c45"/><path d="M5.2 4.2l1.4-.4 1 2.1-.9.8c.4 1 1.2 1.8 2.2 2.3l.8-.9 2.1 1-.4 1.4c-3 .2-6.4-3.2-6.2-6.3z" fill="#fff"/></svg>
    (555)010-0148
  </p>
  <div class="offices">
    <div class="office">
      <svg class="pin" width="18" height="18" viewBox="0 0 16 16" aria-hidden="true"><circle cx="8" cy="8" r="8" fill="#f47c45"/><path d="M8 3.5a3 3 0 0 0-3 3c0 2.2 3 5.5 3 5.5s3-3.3 3-5.5a3 3 0 0 0-3-3z" fill="#fff"/><circle cx="8" cy="6.5" r="1.1" fill="#f47c45"/></svg>
      <div><p class="office__name">Northfield Office</p><p class="office__addr">58 Linden Park Dr. Ste<br>120 Northfield, MD 21700</p></div>
    </div>
    <div class="office">
      <svg class="pin" width="18" height="18" viewBox="0 0 16 16" aria-hidden="true"><circle cx="8" cy="8" r="8" fill="#f47c45"/><path d="M8 3.5a3 3 0 0 0-3 3c0 2.2 3 5.5 3 5.5s3-3.3 3-5.5a3 3 0 0 0-3-3z" fill="#fff"/><circle cx="8" cy="6.5" r="1.1" fill="#f47c45"/></svg>
      <div><p class="office__name">Brookvale Office</p><p class="office__addr">2210 Maple Crest Blvd.<br>Ste. 305 Brookvale, MD 21799</p></div>
    </div>
    <div class="office">
      <svg class="pin" width="18" height="18" viewBox="0 0 16 16" aria-hidden="true"><circle cx="8" cy="8" r="8" fill="#f47c45"/><path d="M8 3.5a3 3 0 0 0-3 3c0 2.2 3 5.5 3 5.5s3-3.3 3-5.5a3 3 0 0 0-3-3z" fill="#fff"/><circle cx="8" cy="6.5" r="1.1" fill="#f47c45"/></svg>
      <div><p class="office__name">Riverton Office</p><p class="office__addr">47 Wellness Way<br>Riverton, WV 25499</p></div>
    </div>
  </div>
  <p class="web-pill">www.bmrfootcare.com</p>
</section>
<p class="size-label size-label--wide">1980 X 1080</p>

</body>
</html>
```